Heating and Cooling Company mobile website

We need a website specifically designed for a viewing on a mobile device.

We serve the northern New Jersey heating, cooling and electrical residential market.

The goal is the drive traffic to the site by using Brintel Pay Per click. People will be searching for an HVAC contractor, and they land on our page. They need to get key info quickly without all the clutter of a desktop type of site.

Target Market(s)

Homeowners

Industry/Entity Type

Hvac

Coding

Coded - Design and coding required

Number of Pages Required

5+ page

Font styles to use
Serif

Requirements
Must have
• View attachments to see samples of the desktop version. It must have a similar color scheme
• The copy of the website is also attached
Nice to have
• Would like it to have a sort of Vardok feel to it. Make it seem like its an app that people are using and that its exciting to be on the website. It would be nice to have a page where customers can book appointments

```html
<!DOCTYPE html>
<html lang="en">
<head>
<meta charset="utf-8">
<title>Hearthline Climate – Mobile Home</title>
<link rel="stylesheet" href="https://fonts.googleapis.com/css2?family=Open+Sans:wght@400;600;700&family=Rubik:wght@500;700&display=swap">
<style>
  :root{
    --page-bg:#ececec;
    --red:#9c2231;
    --red-deep:#861a27;
    --red-text:#a3262f;
    --orange:#f7941d;
    --orange-light:#fbb040;
    --blue:#3d5d98;
    --blue-light:#44659f;
    --blue-dark:#33528a;
    --cream:#f2e4cd;
    --icon:#f6dfa0;
    --ink:#3a3a3a;
    --body:#6b6259;
    --white:#ffffff;
  }
  *{box-sizing:border-box;margin:0;padding:0}
  html,body{width:1200px;height:3500px;overflow:hidden;background:var(--page-bg)}
  body{font-family:"Open Sans",sans-serif;color:var(--ink)}
  .screen{position:absolute;left:250px;top:35px;width:700px;height:3429px;background:var(--white);overflow:hidden;box-shadow:0 0 0 1px #d6d6d6}

  /* hero */
  .hero{position:relative;height:677px;background:var(--cream);text-align:center}
  .hero-photo{position:absolute;inset:0 0 220px 0;background:radial-gradient(ellipse at 50% 55%,#d9b89a 0%,#e9d3b8 45%,#f2e4cd 80%)}
  .brand{position:absolute;top:66px;left:0;right:0;display:flex;justify-content:center;align-items:center;gap:12px}
  .brand-mark{width:22px;height:22px;background:var(--red)}
  .brand-name{font-family:"Rubik",sans-serif;font-weight:700;font-size:34px;color:var(--red)}
  .hero-title{position:absolute;top:440px;left:0;right:0;font-family:"Rubik",sans-serif;font-weight:700;line-height:40px}
  .hero-title .line-blue{display:block;color:var(--blue);font-size:35px;letter-spacing:1px}
  .hero-title .line-red{display:block;color:var(--red-text);font-size:34px;letter-spacing:1px}
  .schedule{position:absolute;top:566px;left:255px;width:190px;height:76px;background:var(--red);border:4px solid var(--orange);border-radius:8px;display:flex;flex-direction:column;justify-content:center;align-items:center;color:var(--white);font-family:"Rubik",sans-serif;font-weight:700;text-decoration:none}
  .schedule b{font-size:24px;letter-spacing:1px;line-height:28px}
  .schedule small{font-size:14px;letter-spacing:1px;line-height:18px}

  /* call bar */
  .call-bar{height:88px;background:var(--orange);display:flex;align-items:center;justify-content:space-between;padding:0 17px 0 21px}
  .menu-btn{width:46px;height:46px;border:2px solid var(--red-text);border-radius:4px;background:#fbd7a2;display:flex;flex-direction:column;justify-content:center;align-items:center;gap:4px}
  .menu-btn span{width:18px;height:3px;background:var(--red-text)}
  .call-number{display:flex;align-items:center;gap:18px;font-weight:700;font-size:30px;color:var(--red-text)}

  .divider{display:block;width:700px;height:139px}

  /* services */
  .services{position:relative;height:1037px;background:var(--white)}
  .service{position:absolute;left:0;right:0;text-align:center}
  .service svg{display:block;margin:0 auto;width:180px;height:180px}
  .service-name{margin-top:20px;font-weight:700;font-size:22px;letter-spacing:1.5px;color:var(--ink)}

  /* news */
  .news{position:relative;height:533px;text-align:center;overflow:hidden}
  .news-photo{position:absolute;inset:0;background:radial-gradient(ellipse at 55% 55%,#e8d9a6 0%,#f1e4c6 50%,#f6ecd9 85%)}
  .news-inner{position:relative;padding-top:46px}
  .news-title{font-family:"Rubik",sans-serif;font-weight:500;font-size:36px;color:var(--blue);letter-spacing:1px}
  .news-item{margin-top:22px}
  .news-date{font-family:"Rubik",sans-serif;font-weight:700;font-size:27px;color:var(--orange)}
  .news-text{margin:8px auto 0;width:600px;font-size:19px;line-height:31px;color:var(--body)}
  .learn-more{display:inline-block;margin-top:10px;font-weight:700;font-size:15px;letter-spacing:1px;color:var(--blue);text-decoration:none}

  /* contact footer */
  .contact{position:relative;height:403px;background:var(--red-deep);border-top:6px solid var(--blue);text-align:center;color:var(--white)}
  .contact-brand{padding-top:24px;font-family:"Rubik",sans-serif;font-weight:700;font-size:28px;color:var(--orange-light)}
  .contact-lines{margin-top:26px;font-size:19px;line-height:32px}
  .contact-lines p{display:flex;justify-content:center;align-items:center;gap:10px}
  .stay{margin-top:24px;font-family:"Rubik",sans-serif;font-weight:700;font-size:23px;color:var(--orange);letter-spacing:1px}
  .social{width:240px;height:64px;margin:14px auto 0;background:var(--orange);border:3px solid var(--orange-light);border-radius:8px;display:flex;justify-content:center;align-items:center;gap:26px}
  .social span{width:24px;height:24px;border-radius:50%;background:var(--white)}

  /* site map */
  .sitemap{height:443px;background:var(--red);color:var(--white);position:relative}
  .col{position:absolute}
  .col h4{font-weight:700;font-size:18px;letter-spacing:1px;margin-bottom:4px}
  .col li{list-style:none;font-size:16.5px;line-height:29.5px}

  .copyright{height:109px;background:var(--orange);color:var(--white);font-size:16px;line-height:30px;display:flex;flex-direction:column;justify-content:center;align-items:center}
</style>
</head>
<body>
<svg width="0" height="0" style="position:absolute">
  <defs>
    <symbol id="badge" viewBox="0 0 180 180">
      <circle cx="90" cy="90" r="86" fill="var(--orange)"/>
      <circle cx="90" cy="90" r="78" fill="var(--red)"/>
    </symbol>
  </defs>
</svg>

<main class="screen">
  <header class="hero">
    <div class="hero-photo" role="img" aria-label="Smiling family behind a company service van"></div>
    <div class="brand"><span class="brand-mark"></span><span class="brand-name">Hearthline Climate</span></div>
    <h1 class="hero-title"><span class="line-blue">MOST TRUSTED</span><span class="line-red">HEATING &amp; COOLING COMPANY</span></h1>
    <a class="schedule" href="#"><b>SCHEDULE</b><small>A SERVICE</small></a>
  </header>

  <nav class="call-bar">
    <div class="menu-btn"><span></span><span></span><span></span></div>
    <div class="call-number">
      <svg width="42" height="42" viewBox="0 0 42 42"><circle cx="21" cy="21" r="19" fill="#fbd7a2" stroke="var(--red-text)" stroke-width="2"/><path d="M14 12 L18 11 L20 17 L17 19 Q19 24 23 26 L25 23 L31 25 L30 29 Q27 32 22 30 Q14 26 12 18 Q12 14 14 12 Z" fill="var(--red-text)"/></svg>
      <span>555-014-2287</span>
    </div>
  </nav>

  <svg class="divider" viewBox="0 0 700 139">
    <rect width="350" height="139" fill="var(--blue-light)"/>
    <rect x="350" width="350" height="139" fill="var(--blue-dark)"/>
    <path d="M256 0 C320 0 349 40 350 96 C351 40 380 0 448 0 Z" fill="var(--orange)"/>
  </svg>

  <section class="services">
    <a class="service" style="top:-20px">
      <svg viewBox="0 0 180 180"><use href="#badge"/><path d="M90 48 C106 70 110 88 100 110 C95 122 80 122 77 108 C74 94 86 88 83 74 C94 80 92 92 92 92 C98 78 98 64 90 48 Z" fill="var(--icon)"/></svg>
      <div class="service-name">HEATING</div>
    </a>
    <a class="service" style="top:244px">
      <svg viewBox="0 0 180 180"><use href="#badge"/><g stroke="var(--icon)" stroke-width="7" stroke-linecap="round"><line x1="90" y1="52" x2="90" y2="128"/><line x1="57" y1="71" x2="123" y2="109"/><line x1="123" y1="71" x2="57" y2="109"/></g><circle cx="90" cy="90" r="11" fill="var(--icon)"/></svg>
      <div class="service-name">AIR CONDITIONING</div>
    </a>
    <a class="service" style="top:508px">
      <svg viewBox="0 0 180 180"><use href="#badge"/><g stroke="var(--icon)" stroke-width="7" fill="none" stroke-linecap="round"><rect x="78" y="54" width="36" height="72"/><line x1="54" y1="72" x2="130" y2="72"/><line x1="54" y1="90" x2="130" y2="90"/><line x1="54" y1="108" x2="130" y2="108"/></g></svg>
      <div class="service-name">OTHER SERVICES</div>
    </a>
    <a class="service" style="top:772px">
      <svg viewBox="0 0 180 180"><use href="#badge"/><g fill="var(--icon)"><circle cx="66" cy="70" r="11"/><circle cx="114" cy="70" r="11"/><circle cx="90" cy="74" r="14"/><rect x="46" y="86" width="38" height="26" rx="12"/><rect x="96" y="86" width="38" height="26" rx="12"/><rect x="66" y="94" width="48" height="32" rx="13"/></g></svg>
      <div class="service-name">WHO WE SERVICES</div>
    </a>
  </section>

  <section class="news">
    <div class="news-photo" role="img" aria-label="Family playing outdoors in a sunny field"></div>
    <div class="news-inner">
      <h2 class="news-title">LATEST NEWS</h2>
      <article class="news-item">
        <div class="news-date">FEB 21</div>
        <p class="news-text">Vestibulum ante ipsum primis in faucibus orci luctus et ultrices posuere nibh eget turpis vehicula tempus ac sed massa..</p>
        <a class="learn-more" href="#">LEARN MORE &#8250;</a>
      </article>
      <article class="news-item">
        <div class="news-date">FEB 21</div>
        <p class="news-text">Vestibulum ante ipsum primis in faucibus orci luctus et ultrices posuere nibh eget turpis vehicula tempus ac sed massa..</p>
        <a class="learn-more" href="#">LEARN MORE &#8250;</a>
      </article>
    </div>
  </section>

  <footer>
    <section class="contact">
      <div class="contact-brand">Hearthline Climate</div>
      <div class="contact-lines">
        <p>48 Alder Court Lakeview, NJ 07000</p>
        <p><svg width="14" height="14" viewBox="0 0 14 14"><path d="M2 1 L5 1 L6 5 L4 6 Q5 9 8 10 L9 8 L13 9 L13 12 Q10 14 6 11 Q2 8 1 4 Z" fill="var(--white)"/></svg>555-014-2287</p>
        <p><svg width="18" height="13" viewBox="0 0 18 13"><rect width="18" height="13" rx="1" fill="var(--white)"/><path d="M1 1 L9 7 L17 1" stroke="var(--red-deep)" stroke-width="1.5" fill="none"/></svg>info@hearthlineclimate.com</p>
      </div>
      <div class="stay">STAY CONNECTED</div>
      <div class="social"><span></span><span></span><span></span><span></span></div>
    </section>

    <section class="sitemap">
      <div class="col" style="left:19px;top:30px"><h4>SITE MAP</h4><ul><li>Home</li><li>About Us</li><li>Services</li><li>Testimonials</li><li>Blog</li><li>Contact Us</li></ul></div>
      <div class="col" style="left:245px;top:30px"><h4>HEATING</h4><ul><li>New Installation</li><li>Repair &amp; Services</li><li>Heat Pumps</li><li>Boilers</li><li>Rediant Heat Systems</li></ul></div>
      <div class="col" style="left:491px;top:30px"><h4>AIR CONDITIONING</h4><ul><li>New Installation</li><li>Repair &amp; Services</li><li>Ductless Systems</li></ul></div>
      <div class="col" style="left:19px;top:266px"><h4>OTHER SERVICES</h4><ul><li>Indoor Air Quality</li><li>Thermostats &amp; Zoning</li><li>Generators</li><li>Products</li></ul></div>
      <div class="col" style="left:245px;top:266px"><h4>WHO WE SERVICES</h4><ul><li>Residentials &amp; Homeowners</li><li>Commercial Businesses</li></ul></div>
    </section>

    <div class="copyright"><span>Copyright© 2017. Company Name</span><span>All Right Reserved</span></div>
  </footer>
</main>
</body>
</html>
```